Moxy Fen needs some awesome stationary

Do you have what it takes to get my brand? You either do or you don't, have a crack at a design and you my just win my business.

I don't want to waste your or my time, so put your creative genius on either a business card or envelope.

I however need a package of stationary that follows the same brand. I will message you to complete the remaining should I like your first submission.

Here is what I need, have a go!

Basically I need the following for my small business based in melbourne.
- Letterhead (printer ready and MS Word)
- Business Card
- Compliments Slip
- Envelope
- Proposal Cover Page (MS Word only)
- Presentation Folder
- Marbled Fox Cards
- Student Name Tent
- Index Cards
- Vell-Ka

I am establishing the brand and it must be modern, professional but also relaxed; that is not formal and not corporate. It represents a company are leaders, but small enough to care and operate like a bunch of friends. We are bringing people and conversations back to business, and turfing out all the bureaucracy and crazy and wasteful procedures. Its about "lets talk and figure it out together and find even better ways".

Target Market(s)

Mainly companies that build software products, but Agile practices are used in many other industries (even graphic design projects)

Industry/Entity Type

Information Technology

Font styles to use
Sans Serif

Colors
3176b5
aaaaaa

Requirements
Must have
• I like curves and circles and not boxes or rectangles.
• I want a colour rich design with my brand colours, but it must be balanced.
• I want more modern than traditional, but simple modern
Should not have
• Not corporate
• Please don't waste my time if your not going to think about it.
• Don't mess with my primary logo
• Don't change my colours
• Don't overlay logo on image

```html
<!DOCTYPE html>
<html lang="en">
<head>
<meta charset="utf-8">
<title>Moxy Fen – Business Card</title>
<link rel="stylesheet" href="https://fonts.googleapis.com/css2?family=Open+Sans:wght@400;600;700&display=swap">
<style>
  :root {
    --brand-blue: #3a5fa8;
    --brand-grey: #939cab;
    --grey-dark: #7d8594;
    --text-grey: #8a8f98;
    --text-dark: #555b64;
    --card-white: #ffffff;
    --backdrop: #ecebe8;
    --rule: #c9ccd2;
  }
  * { box-sizing: border-box; margin: 0; padding: 0; }
  html, body { width: 1200px; height: 950px; overflow: hidden; }
  body {
    background: var(--backdrop);
    font-family: "Open Sans", Arial, sans-serif;
    position: relative;
  }
  .card {
    position: absolute;
    left: 240px;
    width: 720px;
    height: 440px;
    border-radius: 34px;
    overflow: hidden;
    box-shadow: 0 6px 18px rgba(0,0,0,0.12);
  }
  .card--front { top: 40px; background: var(--card-white); }
  .card--back { top: 500px; background: var(--brand-grey); }

  .wordmark {
    position: absolute;
    display: flex;
    align-items: center;
    gap: 18px;
    font-weight: 700;
    white-space: nowrap;
  }
  .wordmark__dot { border-radius: 50%; flex: none; }
  .card--front .wordmark { top: 60px; right: 60px; font-size: 46px; color: var(--brand-blue); }
  .card--front .wordmark__dot { width: 58px; height: 58px; background: var(--brand-grey); }

  .divider {
    position: absolute;
    left: 300px; right: 60px; top: 186px;
    height: 1px; background: var(--rule);
  }
  .address {
    position: absolute;
    right: 60px; top: 206px;
    text-align: right;
    font-size: 19px;
    line-height: 1.35;
    color: var(--text-dark);
  }
  .person { position: absolute; left: 56px; top: 206px; }
  .person__name { font-size: 27px; font-weight: 700; color: var(--brand-blue); }
  .person__role { font-size: 18px; color: var(--text-grey); margin-top: 2px; }
  .contacts {
    position: absolute; left: 56px; top: 290px;
    list-style: none;
    font-size: 17px; color: var(--text-dark); line-height: 1.5;
  }
  .contacts li { display: flex; align-items: center; gap: 10px; }
  .contacts svg { width: 16px; height: 16px; flex: none; }

  .edge-band { position: absolute; left: 0; bottom: 0; width: 720px; height: 44px; }
  .web-front {
    position: absolute; right: 60px; bottom: 10px;
    font-size: 17px; color: var(--card-white); letter-spacing: 0.5px;
  }

  .card--back .wordmark {
    top: 50%; left: 50%; transform: translate(-50%, -50%);
    font-size: 64px; color: var(--card-white);
  }
  .card--back .wordmark__dot { width: 80px; height: 80px; background: var(--card-white); }
  .web-back {
    position: absolute; left: 38px; top: 50%;
    transform: translate(-50%, -50%) rotate(-90deg);
    font-size: 16px; letter-spacing: 5px; color: var(--card-white);
    white-space: nowrap;
  }
</style>
</head>
<body>
  <section class="card card--front" aria-label="Business card front">
    <div class="wordmark"><span class="wordmark__dot"></span><span>Moxy Fen</span></div>
    <div class="divider"></div>
    <address class="address">PO Box 4417<br>Larkfield Vale<br>VIC 3999, Australia</address>
    <div class="person">
      <p class="person__name">Dale Korwin</p>
      <p class="person__role">CEO, Professional Agile Trainer</p>
    </div>
    <ul class="contacts">
      <li><svg viewBox="0 0 16 16"><path d="M3 1h3l1 4-2 1.5a9 9 0 0 0 4.5 4.5L11 9l4 1v3a2 2 0 0 1-2 2A12 12 0 0 1 1 3a2 2 0 0 1 2-2z" fill="var(--brand-blue)"/></svg>1300 555 019</li>
      <li><svg viewBox="0 0 16 16"><rect x="4" y="1" width="8" height="14" rx="1.5" fill="none" stroke="var(--brand-blue)" stroke-width="1.6"/></svg>+61 400 555 182</li>
      <li><svg viewBox="0 0 16 16"><rect x="1" y="3" width="14" height="10" fill="var(--brand-blue)"/><path d="M1 3l7 6 7-6" fill="none" stroke="#fff" stroke-width="1.2"/></svg>dale@moxy-fen.com.au</li>
    </ul>
    <svg class="edge-band" viewBox="0 0 720 44" preserveAspectRatio="none">
      <rect x="0" y="34" width="720" height="10" fill="var(--brand-blue)"/>
      <path d="M0 30 H420 L440 0 H720 V44 H0 Z" fill="var(--brand-blue)"/>
      <path d="M440 0 H720 V44 H412 Z" fill="var(--brand-grey)"/>
    </svg>
    <span class="web-front">www.moxy-fen.com.au</span>
  </section>

  <section class="card card--back" aria-label="Business card back">
    <span class="web-back">www.moxy-fen.com.au</span>
    <div class="wordmark"><span class="wordmark__dot"></span><span>Moxy Fen</span></div>
  </section>
</body>
</html>
```